Home Remodeler Needs a Website!

Single page (plus contact form) website for small home remodeling company. He's got a few pictures he'd like on the site and needs some basic text. He likes clean, simple designs and is "more traditional" in his stylistic preferences. Most of his business comes from word-of-mouth advertising and so the site is just something he needs for people to feel more comfortable with his business.

Target Market(s)

People who want to remodel their homes

Coding

Coded - Design and coding required

Number of Pages Required

2 page

Requirements
Must have
• Main page to include some or all of the attached images, contact page. Neutral colors. Old domain: lindcroftmeadowbuild.com New domain: qm-ventureworks.com You can pull text from the old site or update it.
Should not have
• No loud colors/loud visual elements

```html
<!DOCTYPE html>
<html lang="en">
<head>
<meta charset="utf-8">
<title>Lindcroft Meadow Homes</title>
<link rel="stylesheet" href="https://fonts.googleapis.com/css2?family=Montserrat:wght@600;700;800&family=Lato:wght@400;700&display=swap">
<style>
:root{
  --accent:#a88a5c;
  --accent-soft:#c4ad86;
  --band:#7b6d5a;
  --ink:#262626;
  --dark:#2f2f2f;
  --grey:#666;
  --line:#d6d6d6;
  --white:#fff;
}
*{margin:0;padding:0;box-sizing:border-box}
html,body{width:1200px;height:4906px;overflow:hidden}
body{position:relative;font-family:"Lato",sans-serif;color:var(--ink);background:var(--white)}
.abs{position:absolute}
.head{font-family:"Montserrat",sans-serif;font-weight:800;text-transform:uppercase}
.btn{position:absolute;display:flex;align-items:center;justify-content:center;background:var(--accent);color:var(--white);font-family:"Montserrat",sans-serif;font-weight:700;font-size:12px;text-transform:uppercase}
.photo{position:absolute}

/* header */
.site-header{position:absolute;left:0;top:0;width:1200px;height:62px;background:var(--white)}
.brand{left:110px;top:21px;font-family:"Montserrat",sans-serif;font-weight:700;font-size:16px;letter-spacing:.3px;white-space:nowrap}
.nav{position:absolute;left:400px;top:0;display:flex;gap:32px;height:62px;align-items:center;font-family:"Montserrat",sans-serif;font-weight:600;font-size:11.5px;text-transform:uppercase}
.nav .active{color:var(--accent);position:relative}
.nav .active::after{content:"";position:absolute;left:0;right:0;bottom:-22px;height:3px;background:var(--accent)}
.call-box{position:absolute;left:962px;top:0;width:238px;height:62px;background:var(--accent);color:var(--white);display:flex;align-items:center;justify-content:center;gap:8px;font-size:12px;font-weight:700}

/* hero */
.hero{position:absolute;left:0;top:62px;width:1200px;height:618px;background:linear-gradient(180deg,#8aa3b3 0%,#aebcc2 45%,#5d6d55 75%,#3f4d33 100%)}
.hero-card{left:110px;top:90px;width:475px;height:406px;background:rgba(45,45,45,.92);border:2px solid var(--accent);padding:48px 56px;color:var(--white)}
.hero-card h1{font-size:48px;line-height:52px}
.hero-card p{font-size:13px;line-height:24px;margin-top:18px}
.hero-card .btn{position:static;width:136px;height:48px;margin-top:16px}
.dots{left:1139px;top:270px;display:flex;flex-direction:column;gap:12px}
.dots span{width:11px;height:11px;border-radius:50%;background:var(--white)}
.dots .on{background:var(--accent)}
.slide-num{left:1068px;top:282px;width:30px;height:30px;border-radius:50%;background:var(--accent);color:var(--white);font-size:12px;display:flex;align-items:center;justify-content:center}

/* welcome */
.welcome{position:absolute;left:0;top:680px;width:1200px;height:376px;background:var(--band);color:var(--white)}
.welcome .kicker{left:110px;top:62px;font-family:"Montserrat",sans-serif;font-weight:700;font-size:15px}
.welcome h2{left:110px;top:88px;font-size:48px;line-height:52px;width:560px}
.welcome p{position:absolute;left:112px;width:480px;font-size:12px;line-height:22px}
.welcome-frame{left:648px;top:60px;width:449px;height:260px;border:5px solid var(--white)}

/* services */
.section-kicker{position:absolute;width:1200px;text-align:center;color:var(--accent);font-family:"Montserrat",sans-serif;font-weight:700;font-size:15px}
.section-title{position:absolute;width:1200px;text-align:center;font-size:36px;font-weight:800}
.service{position:absolute;top:1252px;width:312px;text-align:center}
.service .photo{position:relative;width:312px;height:203px}
.service h3{font-size:20px;margin-top:20px}
.service p{font-size:12.5px;line-height:22px;color:var(--grey);margin-top:8px;padding:0 4px}
.service .btn{position:relative;margin:26px auto 0;width:136px;height:46px}
.arrow{position:absolute;top:1428px;width:58px;height:58px;border-radius:50%;display:flex;align-items:center;justify-content:center}

/* about */
.about{position:absolute;left:0;top:1738px;width:1200px;height:498px;background:var(--dark);color:var(--white)}
.about-photo{left:112px;top:1713px;width:451px;height:427px}
.about-corner{left:563px;top:1713px;width:0;height:0;border-left:10px solid var(--accent);border-bottom:25px solid transparent}
.about h2{left:600px;top:80px;font-size:38px}
.about p{position:absolute;left:600px;width:488px;font-size:12.5px;line-height:22px;text-align:justify}

/* contracting */
.tile{position:absolute;display:flex;align-items:flex-end;justify-content:center;padding:0 20px 18px;color:var(--white);text-align:center;font-family:"Montserrat",sans-serif;font-weight:700;font-size:18px;line-height:26px;text-transform:uppercase}

/* resource */
.resource{position:absolute;left:0;top:3155px;width:1200px;height:576px;background:linear-gradient(120deg,#3a3a38 0%,#8f9b9e 45%,#c3cdd0 65%,#6b6660 100%)}
.resource-box{left:112px;top:95px;width:488px;height:410px;background:rgba(245,245,245,.94);padding:16px}
.resource-frame{width:100%;height:100%;border:2px solid var(--accent);text-align:center;padding:36px 30px 0}
.resource-frame h2{font-size:34px}
.resource-frame p{font-size:12.5px;line-height:22px;color:var(--grey);margin-top:14px}
.resource-frame .btn{position:relative;margin:22px auto 0;width:134px;height:46px}

/* contact */
.info{position:absolute;top:3880px;display:flex;gap:14px;align-items:flex-start}
.info .ic{width:56px;height:56px;border-radius:50%;background:var(--accent);display:flex;align-items:center;justify-content:center;flex:none}
.info small{display:block;font-size:13px;font-weight:700;margin-top:4px}
.info b{display:block;font-size:18px;font-weight:700;line-height:26px}
.field{position:absolute;border:1px solid var(--line);color:#888;font-size:12.5px;padding:22px 34px}
.captcha{left:712px;top:4380px;width:153px;height:42px;border:1px solid var(--line);background:#f9f9f9;display:flex;align-items:center;gap:8px;padding:0 8px;font-size:8px;color:var(--grey)}

/* footer */
.footer{position:absolute;left:0;top:4560px;width:1200px;height:346px;background:var(--dark);border-top:4px solid var(--accent);color:var(--white)}
.footer h4{font-family:"Montserrat",sans-serif;font-weight:700;font-size:17px;line-height:26px;position:relative}
.footer h4::after{content:"";position:absolute;left:0;bottom:-10px;width:28px;height:2px;background:var(--accent)}
.fcol{position:absolute;top:58px}
.fcol ul{list-style:none;margin-top:24px;font-size:13px;line-height:26px}
.fcol p{margin-top:24px;font-size:13px;line-height:23px;width:240px}
.socials{display:flex;gap:10px;margin-top:26px}
.socials span{width:36px;height:36px;border:2px solid var(--white);border-radius:50%;display:block}
.copy{left:0;top:310px;width:1200px;text-align:center;font-size:12px}
</style>
</head>
<body>

<header class="site-header">
  <div class="abs brand">LINDCROFT MEADOW HOMES</div>
  <nav class="nav">
    <span class="active">Home</span><span>About Us</span><span>Services</span><span>Package</span><span>Resources</span><span>Contact Us</span>
  </nav>
  <div class="call-box">
    <svg width="12" height="12" viewBox="0 0 24 24"><path fill="#fff" d="M6.6 10.8a15 15 0 0 0 6.6 6.6l2.2-2.2c.3-.3.7-.4 1-.2 1.1.4 2.3.6 3.6.6.6 0 1 .4 1 1V20c0 .6-.4 1-1 1A17 17 0 0 1 3 4c0-.6.4-1 1-1h3.5c.6 0 1 .4 1 1 0 1.3.2 2.5.6 3.6.1.3 0 .7-.2 1z"/></svg>
    +1 800 555 0199
  </div>
</header>

<section class="hero" role="img" aria-label="Photo of a grey two-storey house with a pale roof under a cloudy sky, lawn and shrubs in front">
  <div class="abs hero-card">
    <h1 class="head">Lindcroft<br>Meadow<br>Homes</h1>
    <p>When you want affordable, quality home construction services; think of us to do the job.</p>
    <div class="btn">Get a Quote</div>
  </div>
  <div class="abs slide-num">2</div>
  <div class="abs dots"><span></span><span class="on"></span><span></span><span></span></div>
</section>

<section class="welcome">
  <div class="abs kicker">WELCOME</div>
  <h2 class="abs head">Lindcroft Meadow Homes</h2>
  <p style="top:216px">When you want affordable, quality home construction services; think of us to do the job.</p>
  <p style="top:260px">Since 1981 Gordon Avery has built and remodeled over 400 homes and businesses. Let us be your contractor for the next project you start.</p>
  <div class="abs welcome-frame" role="img" aria-label="Photo of a kitchen with dark wood cabinets and bar stools" style="background:linear-gradient(100deg,#3b2a3e 0%,#5a3a28 35%,#2a1d16 70%,#171414 100%)"></div>
</section>

<div class="section-kicker" style="top:1146px">SERVICES</div>
<h2 class="section-title head" style="top:1178px">What We Do</h2>

<div class="arrow" style="left:76px;background:#ececec">
  <svg width="16" height="16" viewBox="0 0 24 24"><path d="M15 5l-7 7 7 7" fill="none" stroke="#333" stroke-width="2.5"/></svg>
</div>
<article class="service" style="left:112px">
  <div class="photo" role="img" aria-label="Photo of a roofer laying dark shingles on a house roof" style="background:linear-gradient(180deg,#c9d4df 0%,#8f8a84 45%,#3c3a3a 100%)"></div>
  <h3 class="head">Roofing</h3>
  <p>Lorem ipsum dolor sit amet, consectetur adipiscing elit, sed do eiusmod tempor incididunt ut labore et dolore magna aliqua.</p>
  <div class="btn">Learn More</div>
</article>
<article class="service" style="left:444px">
  <div class="photo" role="img" aria-label="Photo of a worker fitting a new white window frame" style="background:linear-gradient(90deg,#6b4a36 0%,#d9dcd8 40%,#9fbf8a 80%,#e5e5e2 100%)"></div>
  <h3 class="head">Window Replacement</h3>
  <p>Lorem ipsum dolor sit amet, consectetur adipiscing elit, sed do eiusmod tempor incididunt ut labore et dolore magna aliqua.</p>
  <div class="btn">Learn More</div>
</article>
<article class="service" style="left:776px">
  <div class="photo" role="img" aria-label="Photo of hands testing wiring in an electrical panel" style="background:linear-gradient(160deg,#d9d1b8 0%,#b8ad7a 45%,#9c8a5a 70%,#8a8a86 100%)"></div>
  <h3 class="head">Electrical</h3>
  <p>Lorem ipsum dolor sit amet, consectetur adipiscing elit, sed do eiusmod tempor incididunt ut labore et dolore magna aliqua.</p>
  <div class="btn">Learn More</div>
</article>
<div class="arrow" style="left:1062px;background:var(--accent)">
  <svg width="16" height="16" viewBox="0 0 24 24"><path d="M9 5l7 7-7 7" fill="none" stroke="#fff" stroke-width="2.5"/></svg>
</div>

<section class="about">
  <h2 class="abs head">About Us</h2>
  <p style="top:142px">With over 20 years experience in residential and commercial construction, you can trust your project to Lindcroft Meadow Homes.</p>
  <p style="top:196px">"DON'T TINKER AROUND"</p>
  <p style="top:240px">I have built my business with a partnership of clients, employees, subcontractors, suppliers and inspectors. Since each project is unique, this partnership brings creative ideas to your home. I have deep "hands on" history in construction from foundations to final finishing touches. We cultivate suppliers who deliver quality materials on time and without damage. Our subcontractors are our friends and will become yours too. When called upon to explain their part of the process, they are glad to.</p>
</section>
<div class="photo about-photo" role="img" aria-label="Photo of a kitchen with a stainless steel fridge, blue wall and wood floor" style="background:linear-gradient(110deg,#2e416a 0%,#8d8f92 35%,#c9c6bf 60%,#4a3425 100%)"></div>
<div class="abs about-corner"></div>

<h2 class="section-title head" style="top:2318px;font-size:33px;line-height:44px">Commercial and Residential<br>Contracting</h2>
<div class="tile" style="left:112px;top:2434px;width:315px;height:273px;background:linear-gradient(180deg,#e4e2dd 0%,#a9a39a 55%,#4a4540 100%)" role="img" aria-label="Photo of a bright living room with a staircase">Pre Construction<br>Consultation</div>
<div class="tile" style="left:444px;top:2434px;width:313px;height:334px;background:linear-gradient(180deg,#c8d3dc 0%,#8c7d6a 50%,#3c3a36 100%)" role="img" aria-label="Photo of builders in hard hats at a building under scaffolding">New Construction</div>
<div class="tile" style="left:773px;top:2434px;width:315px;height:273px;background:linear-gradient(180deg,#f0ece4 0%,#c7b89c 55%,#5a5046 100%)" role="img" aria-label="Photo of a white kitchen with pendant lights">Remodeling / Kitchens<br>and Baths</div>
<div class="tile" style="left:112px;top:2725px;width:315px;height:334px;background:linear-gradient(180deg,#dde3e6 0%,#6f8456 50%,#3a3a38 100%)" role="img" aria-label="Photo of a screened porch addition with a dining table">Additions</div>
<div class="tile" style="left:444px;top:2786px;width:313px;height:273px;background:linear-gradient(180deg,#6f8a4a 0%,#8a5a36 55%,#3e3a32 100%)" role="img" aria-label="Photo of a wooden pergola deck among trees">Porches and Decks</div>
<div class="tile" style="left:773px;top:2725px;width:315px;height:334px;background:linear-gradient(180deg,#e8e6e2 0%,#b49478 55%,#4e463e 100%)" role="img" aria-label="Photo of hands reviewing plans in a renovated hallway">Specializing in Historic<br>Renovations.</div>

<section class="resource" role="img" aria-label="Photo of a bathroom with a soaking tub, tiled wall and towel">
  <div class="abs resource-box">
    <div class="resource-frame">
      <h2 class="head">Resource</h2>
      <p>Lorem ipsum dolor sit amet, consectetur adipiscing elit, sed do eiusmod tempor incididunt ut labore et dolore magna aliqua. Ut enim ad minim veniam, quis nostrud exercitation ullamco laboris nisi ut aliquip ex ea commodo consequat. Duis aute irure dolor in reprehenderit in voluptate velit esse cillum dolore eu fugiat nulla pariatur. Excepteur sint occaecat cupidatat non proident, sunt in culpa qui officia deserunt mollit anim id est laborum.</p>
      <div class="btn">Learn More</div>
    </div>
  </div>
</section>

<h2 class="section-title head" style="top:3818px">Contact Us</h2>
<div class="info" style="left:205px">
  <div class="ic"><svg width="22" height="22" viewBox="0 0 24 24"><path fill="#fff" d="M6.6 10.8a15 15 0 0 0 6.6 6.6l2.2-2.2c.3-.3.7-.4 1-.2 1.1.4 2.3.6 3.6.6.6 0 1 .4 1 1V20c0 .6-.4 1-1 1A17 17 0 0 1 3 4c0-.6.4-1 1-1h3.5c.6 0 1 .4 1 1 0 1.3.2 2.5.6 3.6.1.3 0 .7-.2 1z"/></svg></div>
  <div><small>Call us Today :</small><b>615-555-0148</b></div>
</div>
<div class="info" style="left:472px">
  <div class="ic"><svg width="22" height="22" viewBox="0 0 24 24"><rect x="3" y="5" width="18" height="14" rx="2" fill="#fff"/><path d="M3 7l9 6 9-6" fill="none" stroke="#a88a5c" stroke-width="2"/></svg></div>
  <div><small>Mail us :</small><b>info@companyname</b></div>
</div>
<div class="info" style="left:762px">
  <div class="ic"><svg width="22" height="22" viewBox="0 0 24 24"><path fill="#fff" d="M12 2a7 7 0 0 0-7 7c0 5 7 13 7 13s7-8 7-13a7 7 0 0 0-7-7zm0 9.5A2.5 2.5 0 1 1 12 6.5a2.5 2.5 0 0 1 0 5z"/></svg></div>
  <div><small>Address :</small><b>Lorem ipsum dolor sit<br>amet, consectetur</b></div>
</div>

<div class="field" style="left:248px;top:4000px;width:342px;height:63px">Name*</div>
<div class="field" style="left:608px;top:4000px;width:342px;height:63px">Email address*</div>
<div class="field" style="left:248px;top:4077px;width:342px;height:63px">Phone*</div>
<div class="field" style="left:608px;top:4077px;width:342px;height:63px">Subject*</div>
<div class="field" style="left:248px;top:4155px;width:702px;height:200px">Message*</div>
<div class="btn" style="left:512px;top:4378px;width:174px;height:50px;font-size:13px">Submit</div>
<div class="abs captcha">
  <svg width="18" height="18" viewBox="0 0 24 24"><path d="M4 12l5 5 11-11" fill="none" stroke="#5a7a5e" stroke-width="3"/></svg>
  <span>I'm not a robot</span>
  <span style="margin-left:auto;width:18px;height:18px;border-radius:50%;background:#c8ccd4"></span>
</div>

<footer class="footer">
  <div class="fcol" style="left:110px">
    <h4>Lindcroft Meadow<br>Homes.</h4>
    <p>Lorem ipsum dolor sit amet, consectetur adipiscing elit, sed do eiusmod tempor incididunt ut labore et dolore magna aliqua. Ut enim ad minim veniam</p>
  </div>
  <div class="fcol" style="left:398px">
    <h4>Sitemap</h4>
    <ul><li>Home</li><li>About</li><li>Services</li><li>Package</li><li>Blog</li><li>Contact Us</li></ul>
  </div>
  <div class="fcol" style="left:655px">
    <h4>Services</h4>
    <ul><li>Roofing</li><li>Window Replacement</li><li>Electrical</li><li>Air Conditioning &amp; Plumbing</li><li>Painting</li><li>Gutters, Concrete Work</li></ul>
  </div>
  <div class="fcol" style="left:914px">
    <h4>Social with us</h4>
    <div class="socials"><span></span><span></span><span></span><span></span></div>
  </div>
  <div class="abs copy">© Copyrights 2021 Company name | All Rights Reserved</div>
</footer>

</body>
</html>
```